A clean crisp business card for a Landscape Construction company. Designed to be easy to read contact/ info and also be appealing/interesting, unlike a traditional business card.

Industry/Entity Type

Landscape Construction

Contact Information for Business Card

Company name : Brambleford Landscape Construction, phone number: (877) 62Vista, website:Bramblefordyards.example, Email, sales@bramblefordyards.example

Requirements
Nice to have
• Luxurious finishes/ details…. Icons or emblems next to contact info
Should not have
• Clipart or general pictures

```html
<!DOCTYPE html>
<html lang="en">
<head>
<meta charset="utf-8">
<title>Brambleford Landscape Construction – Business Card</title>
<link rel="stylesheet" href="https://fonts.googleapis.com/css2?family=Cinzel:wght@600&family=Roboto+Condensed:wght@400;700&display=swap">
<style>
  :root {
    --backdrop: #d9d9d9;
    --card: #1c1c1d;
    --card-edge: #262627;
    --silver: #c9c9c9;
    --silver-bright: #e6e6e6;
    --silver-dim: #8d8d8d;
  }
  * { box-sizing: border-box; margin: 0; padding: 0; }
  html, body {
    width: 1200px;
    height: 800px;
    overflow: hidden;
    background: var(--backdrop);
  }
  .canvas {
    position: relative;
    width: 1200px;
    height: 800px;
    display: flex;
    align-items: center;
    justify-content: center;
    gap: 60px;
  }
  .card {
    position: relative;
    width: 510px;
    height: 295px;
    border-radius: 22px;
    background: var(--card);
    border: 1px solid var(--card-edge);
    overflow: hidden;
  }

  /* Contact side */
  .card--contact .brand-block {
    position: absolute;
    left: 30px;
    top: 62px;
    width: 168px;
    display: flex;
    flex-direction: column;
    align-items: flex-end;
    gap: 10px;
  }
  .brand-dot {
    width: 14px;
    height: 14px;
    border-radius: 50%;
    background: var(--silver);
  }
  .brand-name--small {
    font-family: "Cinzel", serif;
    font-weight: 600;
    font-size: 16px;
    line-height: 1.25;
    letter-spacing: 1px;
    color: var(--silver);
    text-align: right;
  }
  .person {
    position: absolute;
    left: 30px;
    bottom: 56px;
    width: 168px;
    text-align: right;
    font-family: "Roboto Condensed", sans-serif;
  }
  .person__name {
    font-weight: 700;
    font-size: 18px;
    letter-spacing: 1px;
    color: var(--silver-bright);
  }
  .person__title {
    font-size: 12px;
    letter-spacing: 1.5px;
    color: var(--silver-dim);
    margin-top: 2px;
  }
  .divider {
    position: absolute;
    left: 214px;
    top: 150px;
    width: 1px;
    height: 92px;
    background: var(--silver-dim);
  }
  .contact-list {
    position: absolute;
    left: 230px;
    top: 158px;
    width: 260px;
    list-style: none;
    font-family: "Roboto Condensed", sans-serif;
    font-size: 12px;
    letter-spacing: 0.5px;
    color: var(--silver);
    text-transform: uppercase;
  }
  .contact-list li {
    display: flex;
    align-items: center;
    gap: 8px;
    height: 26px;
    white-space: nowrap;
  }
  .contact-list svg {
    width: 12px;
    height: 12px;
    flex: none;
    fill: none;
    stroke: var(--silver);
    stroke-width: 1.6;
  }

  /* Brand side */
  .card--brand {
    display: flex;
    flex-direction: column;
    align-items: center;
    justify-content: center;
    gap: 18px;
  }
  .card--brand .brand-dot {
    width: 26px;
    height: 26px;
  }
  .brand-name--large {
    font-family: "Cinzel", serif;
    font-weight: 600;
    font-size: 40px;
    letter-spacing: 1px;
    color: var(--silver);
    text-align: center;
    line-height: 1.1;
  }
  .brand-tagline {
    font-family: "Cinzel", serif;
    font-weight: 600;
    font-size: 19px;
    letter-spacing: 4px;
    color: var(--silver);
    text-align: center;
    margin-top: -8px;
  }
</style>
</head>
<body>
<main class="canvas">

  <section class="card card--contact">
    <div class="brand-block">
      <span class="brand-dot"></span>
      <p class="brand-name--small">Brambleford Landscape Construction</p>
    </div>

    <div class="person">
      <p class="person__name">DANIEL HARTLEY</p>
      <p class="person__title">PRESIDENT</p>
    </div>

    <span class="divider"></span>

    <ul class="contact-list">
      <li>
        <svg viewBox="0 0 16 16" aria-hidden="true"><path d="M4 1.5 L6.5 4.5 L5 6.5 Q6.5 9.5 9.5 11 L11.5 9.5 L14.5 12 L12.5 14.5 Q5 13.5 1.5 4 Z"/></svg>
        <span>(877) 62Vista</span>
      </li>
      <li>
        <svg viewBox="0 0 16 16" aria-hidden="true"><rect x="1.5" y="3.5" width="13" height="9" rx="1"/><path d="M1.5 4 L8 9 L14.5 4"/></svg>
        <span>sales@bramblefordyards.example</span>
      </li>
      <li>
        <svg viewBox="0 0 16 16" aria-hidden="true"><circle cx="8" cy="8" r="6.5"/><ellipse cx="8" cy="8" rx="2.8" ry="6.5"/><path d="M1.5 8 H14.5"/></svg>
        <span>Bramblefordyards.example</span>
      </li>
    </ul>
  </section>

  <section class="card card--brand">
    <span class="brand-dot"></span>
    <p class="brand-name--large">Brambleford</p>
    <p class="brand-tagline">Landscape Construction</p>
  </section>

</main>
</body>
</html>
```